I need a label design to go on our jars of honey. Our company is called Marrowdale Honey Co. The type of honey is called Fernlight Glen Honey. The jars are 1kg. Attached is the label size. Left hand side needs to have nutritional info... as attached. Middle section is our company name, honey type, 1kg & Whangamata, NZ. Right hand side needs to have info as per photo (raw honey etc). I would like to upload more pictures... but I’m unsure how to do this? Thanks, Carla

Target Market(s)

Honey consumers... families

Industry/Entity Type

Food Production

Colors

Designer to choose colors to be used in the design.

Requirements
Must have
• Nutritional info as per upload
• Type of honey & company name as per upload
• 1kg
• Address
Nice to have
• Similar fonts to upload.
• Possibly background image... floral or beach... very faint though.

```html
<!DOCTYPE html>
<html lang="en">
<head>
<meta charset="utf-8">
<title>Marrowdale Honey Co. – Fernlight Glen Honey Label</title>
<link href="https://fonts.googleapis.com/css2?family=Amatic+SC:wght@400;700&family=Kaushan+Script&family=Patrick+Hand&family=Roboto+Condensed:wght@400;700&family=Open+Sans:wght@400;600&display=swap" rel="stylesheet">
<style>
  :root {
    --label-pink: #d87aa0;
    --label-pink-light: #e59bbb;
    --label-pink-deep: #c9628c;
    --panel-rose: #b8456f;
    --ink: #ffffff;
  }
  * { box-sizing: border-box; margin: 0; padding: 0; }
  html, body { width: 1200px; height: 605px; overflow: hidden; background: #ffffff; }
  .label {
    position: relative;
    width: 1200px;
    height: 605px;
    color: var(--ink);
    overflow: hidden;
  }
  .label__backdrop {
    position: absolute;
    inset: 0;
    background:
      radial-gradient(ellipse 420px 320px at 600px 300px, var(--label-pink-light), transparent 75%),
      linear-gradient(90deg, var(--label-pink-deep), var(--label-pink) 30%, var(--label-pink) 70%, var(--label-pink-deep));
  }

  /* Left column */
  .facts {
    position: absolute;
    font-family: "Open Sans", sans-serif;
    text-align: center;
    white-space: nowrap;
  }
  .facts__claim { top: 52px; left: 47px; width: 243px; font-size: 16px; line-height: 21px; }
  .nutrition {
    position: absolute;
    top: 107px;
    left: 47px;
    width: 243px;
    height: 262px;
    border: 2px solid var(--ink);
    font-family: "Roboto Condensed", sans-serif;
  }
  .nutrition__title {
    font-family: "Open Sans", sans-serif;
    font-size: 15px;
    font-weight: 400;
    text-align: center;
    padding: 5px 0 4px;
    border-bottom: 2px solid var(--ink);
  }
  .nutrition__serving {
    font-size: 12.5px;
    font-weight: 700;
    line-height: 15px;
    padding: 6px 8px 5px;
    border-bottom: 1.5px solid var(--ink);
  }
  .nutrition table { width: 100%; border-collapse: collapse; font-size: 12.5px; font-weight: 700; }
  .nutrition th {
    font-size: 11px;
    font-weight: 700;
    text-align: left;
    padding: 7px 0 5px 8px;
    border-bottom: 1.5px solid var(--ink);
  }
  .nutrition td { padding: 3px 0 3px 8px; line-height: 15.5px; }
  .nutrition tr:nth-child(2) td { padding-top: 9px; }
  .facts__storage {
    top: 393px;
    left: 28px;
    width: 282px;
    font-size: 15px;
    line-height: 19px;
    letter-spacing: -0.1px;
  }
  .batch {
    position: absolute;
    top: 480px;
    left: 47px;
    width: 243px;
    height: 83px;
    border: 2px solid var(--ink);
    background: var(--panel-rose);
    font-family: "Open Sans", sans-serif;
    font-size: 15px;
    line-height: 20px;
    padding: 7px 9px;
  }

  /* Centre */
  .brand {
    position: absolute;
    left: 380px;
    width: 440px;
    top: 58px;
    text-align: center;
    font-family: "Amatic SC", sans-serif;
    font-weight: 400;
    font-size: 60px;
    line-height: 58px;
    letter-spacing: 14px;
  }
  .variety {
    position: absolute;
    left: 330px;
    width: 540px;
    top: 248px;
    text-align: center;
    font-family: "Kaushan Script", cursive;
    font-size: 64px;
    line-height: 82px;
  }
  .weight {
    position: absolute;
    left: 450px;
    width: 300px;
    top: 481px;
    text-align: center;
    font-family: "Amatic SC", sans-serif;
    font-size: 34px;
  }
  .origin {
    position: absolute;
    left: 400px;
    width: 400px;
    top: 529px;
    text-align: center;
    font-family: "Amatic SC", sans-serif;
    font-weight: 700;
    font-size: 36px;
    letter-spacing: 1px;
  }

  /* Right column */
  .story {
    position: absolute;
    left: 900px;
    width: 262px;
    text-align: center;
    font-family: "Patrick Hand", cursive;
    font-size: 17.5px;
    line-height: 23px;
    white-space: nowrap;
  }
  .story--source { top: 75px; }
  .story--raw { top: 150px; }
  .story--signoff { top: 256px; }
  .story--meaning { top: 353px; }
  .story--contact { top: 460px; line-height: 21px; }
</style>
</head>
<body>
<main class="label">
  <div class="label__backdrop" role="img" aria-label="Faint pink floral and leaf pattern radiating from the centre of the label"></div>

  <p class="facts facts__claim">100% New Zeland Honey<br>No added ingredients</p>

  <section class="nutrition" aria-label="Nutritional information">
    <h2 class="nutrition__title">NUTRITIONAL INFORMATION</h2>
    <p class="nutrition__serving">Servings per package: 100<br>Serving size: 10g</p>
    <table>
      <tr><th>Average Quantity</th><th>per Serving</th><th>per 100g</th></tr>
      <tr><td>Energy</td><td>134kj</td><td>1340kj</td></tr>
      <tr><td>Protein</td><td>0.04g</td><td>0.4g</td></tr>
      <tr><td>Fat total</td><td>0g</td><td>0g</td></tr>
      <tr><td>&nbsp;- saturated</td><td>0g</td><td>0g</td></tr>
      <tr><td>Carbohydrate</td><td>7.9g</td><td>79g</td></tr>
      <tr><td>&nbsp;- sugars</td><td>7.8g</td><td>78.1g</td></tr>
      <tr><td>Sodium</td><td>1.2mg</td><td>12mg</td></tr>
    </table>
  </section>

  <p class="facts facts__storage">Store upright in a cool, dry place.<br>No refrigeration needed.<br>Not recomended for infants<br>below the age of 12 months.</p>

  <div class="batch">Best before:<br>RMP:<br>Batch No:</div>

  <h1 class="brand">Marrowdale<br>Honey Co.</h1>
  <p class="variety">Fernlight Glen<br>Honey</p>
  <p class="weight">1kg</p>
  <p class="origin">Whangamata, NZ</p>

  <p class="story story--source">Sourced from the beautiful<br>Coromandel Pensinula.</p>
  <p class="story story--raw">Our honey comes to you raw &amp;<br>unpasterurised, ensured it retains<br>all the natural goodness!</p>
  <p class="story story--signoff">Arohanui,<br>Russell, Carla &amp; boys</p>
  <p class="story story--meaning">'Marrowdale' - all thanks to God for<br>His incredible creation!</p>
  <p class="story story--contact">www.marrowdalehoney.co.nz<br>42 Kereru Lane<br>Whangamata<br>New Zeland</p>
</main>
</body>
</html>
```